NEW Modern Sleek Business Card for VR Language Startup

Our startup is using VR to lead the next wave of world language education. We need a two-sided business card that introduces the larger organization (Brightloom Language Inc) and our contact info on one side and shows the product, Glimwoorld, on the other side.

Side 1 (contact info)= Brightloom Logo and Contact info (name, title, phone, email)

Side 2 (product)= Glimworld logo, text, and website
Text= Culturally Immersive Language Learning Games
Website= www.glimworld-play.com

Target Market(s)

Education, Technology

Contact Information for Business Card

Contact info will be updated upon approval of the design. For now, put this as a placeholder.

Perry Dunmore
Founder & CEO
pdunmore@quillpost-mail.net
(555)-014-2286

Font styles to use
Other font styles liked:
• Gibson and Century Gothic are the brand fonts

Requirements
Nice to have
• I would love to see cohesion between the design and colors of the two logos. I have attached a few business card designs that I like, so you can get a feel for my preferred style.

```html
<!DOCTYPE html>
<html lang="en">
<head>
<meta charset="utf-8">
<title>Brightloom Language &amp; Glimworld Business Cards</title>
<link href="https://fonts.googleapis.com/css2?family=Questrial&family=Montserrat:wght@500;700&display=swap" rel="stylesheet">
<style>
  :root {
    --backdrop: #2a2a2c;
    --card-top: #ffffff;
    --card-bottom: #e6e6e8;
    --ink: #2e2e33;
    --orange: #f07a2a;
    --red: #e5263d;
    --magenta: #b22fa8;
    --violet: #6a3fe0;
    --blue: #3f6fe6;
    --teal: #22c6d3;
    --title-red: #ffe3e6;
    --white: #ffffff;
    --swoosh: #141414;
  }
  * { box-sizing: border-box; margin: 0; padding: 0; }
  html, body { width: 1200px; height: 997px; overflow: hidden; }
  body {
    background: var(--backdrop);
    font-family: "Questrial", "Century Gothic", sans-serif;
    color: var(--ink);
    position: relative;
  }
  .card {
    position: absolute;
    top: 340px;
    width: 520px;
    height: 300px;
    border-radius: 24px;
    overflow: hidden;
    background: linear-gradient(160deg, var(--card-top) 0%, var(--card-bottom) 100%);
    box-shadow: 0 18px 40px rgba(0,0,0,.55);
  }
  .card--contact { left: 55px; }
  .card--product { left: 625px; }
  .card__swoosh { position: absolute; inset: 0; width: 100%; height: 100%; }

  .brand { position: absolute; display: flex; align-items: center; gap: 12px; }
  .brand__dot { border-radius: 50%; flex: none; }
  .brand__name { font-family: "Questrial", "Century Gothic", sans-serif; color: var(--ink); white-space: nowrap; }

  /* contact side */
  .card--contact .brand { left: 32px; top: 48px; }
  .card--contact .brand__dot {
    width: 32px; height: 32px;
    background: linear-gradient(135deg, var(--orange), var(--magenta), var(--blue));
  }
  .card--contact .brand__name { font-size: 20px; letter-spacing: 2px; text-transform: uppercase; }

  .person { position: absolute; left: 110px; top: 218px; width: 180px; text-align: center; }
  .person__name {
    font-family: "Montserrat", "Gibson", sans-serif;
    font-weight: 700; font-size: 13px; letter-spacing: .5px; color: var(--ink);
  }
  .person__title {
    font-family: "Montserrat", "Gibson", sans-serif;
    font-weight: 500; font-size: 11px; color: var(--title-red); margin-top: 3px;
  }

  .contact-divider {
    position: absolute; left: 318px; top: 136px; width: 1px; height: 70px;
    background: rgba(255,255,255,.55);
  }
  .contact-list { position: absolute; left: 332px; top: 136px; list-style: none; }
  .contact-list__item {
    display: flex; align-items: center; gap: 9px;
    font-size: 11.5px; color: var(--white); height: 23px;
  }
  .contact-list__icon { width: 12px; height: 12px; fill: var(--white); flex: none; }

  /* product side */
  .card--product .brand { left: 0; right: 0; top: 30px; flex-direction: column; gap: 10px; }
  .card--product .brand__dot {
    width: 80px; height: 80px;
    background: linear-gradient(135deg, var(--teal), var(--blue) 55%, var(--violet));
  }
  .card--product .brand__name { font-size: 40px; letter-spacing: 1px; line-height: 1; }
  .tagline {
    position: absolute; left: 0; right: 0; top: 172px; text-align: center;
    font-size: 13px; color: var(--ink); letter-spacing: .2px;
  }
  .website {
    position: absolute; left: 0; right: 0; bottom: 22px; text-align: center;
    font-size: 14px; letter-spacing: 2px; color: var(--white);
  }
</style>
</head>
<body>

  <section class="card card--contact" aria-label="Brightloom Language contact side">
    <svg class="card__swoosh" viewBox="0 0 520 300" preserveAspectRatio="none" aria-hidden="true">
      <defs>
        <linearGradient id="spectrum" x1="0" y1="1" x2="1" y2="0">
          <stop offset="0" stop-color="var(--orange)"/>
          <stop offset=".28" stop-color="var(--red)"/>
          <stop offset=".5" stop-color="var(--magenta)"/>
          <stop offset=".68" stop-color="var(--violet)"/>
          <stop offset=".85" stop-color="var(--blue)"/>
          <stop offset="1" stop-color="var(--teal)"/>
        </linearGradient>
      </defs>
      <path d="M0 300 L0 272 C120 192 300 112 520 94 L520 300 Z" fill="url(#spectrum)"/>
      <path d="M92 210 C190 146 320 104 470 88 C330 112 210 152 92 210 Z" fill="var(--swoosh)"/>
    </svg>

    <div class="brand">
      <span class="brand__dot"></span>
      <span class="brand__name">Brightloom Language</span>
    </div>

    <div class="person">
      <p class="person__name">PERRY DUNMORE</p>
      <p class="person__title">Founder &amp; CEO</p>
    </div>

    <span class="contact-divider"></span>
    <ul class="contact-list">
      <li class="contact-list__item">
        <svg class="contact-list__icon" viewBox="0 0 24 24"><path d="M6.6 10.8a15.1 15.1 0 0 0 6.6 6.6l2.2-2.2a1 1 0 0 1 1-.25 11.4 11.4 0 0 0 3.6.57 1 1 0 0 1 1 1V20a1 1 0 0 1-1 1A17 17 0 0 1 3 4a1 1 0 0 1 1-1h3.5a1 1 0 0 1 1 1c0 1.250.2 2.45.57 3.57a1 1 0 0 1-.25 1z"/></svg>
        07150142
      </li>
      <li class="contact-list__item">
        <svg class="contact-list__icon" viewBox="0 0 24 24"><path d="M6.6 10.8a15.1 15.1 0 0 0 6.6 6.6l2.2-2.2a1 1 0 0 1 1-.25 11.4 11.4 0 0 0 3.6.57 1 1 0 0 1 1 1V20a1 1 0 0 1-1 1A17 17 0 0 1 3 4a1 1 0 0 1 1-1h3.5a1 1 0 0 1 1 1c0 1.250.2 2.45.57 3.57a1 1 0 0 1-.25 1z"/></svg>
        06550286
      </li>
      <li class="contact-list__item">
        <svg class="contact-list__icon" viewBox="0 0 24 24"><path d="M2 5h20v14H2zm2 2v.5l8 5 8-5V7l-8 5z"/></svg>
        care@brightloom.net
      </li>
    </ul>
  </section>

  <section class="card card--product" aria-label="Glimworld product side">
    <svg class="card__swoosh" viewBox="0 0 520 300" preserveAspectRatio="none" aria-hidden="true">
      <defs>
        <linearGradient id="ocean" x1="0" y1="1" x2="1" y2="0">
          <stop offset="0" stop-color="var(--teal)"/>
          <stop offset=".55" stop-color="var(--blue)"/>
          <stop offset="1" stop-color="var(--violet)"/>
        </linearGradient>
      </defs>
      <path d="M0 300 C150 244 330 214 520 206 L520 300 Z" fill="url(#ocean)"/>
      <path d="M40 280 C160 234 330 206 480 198 C330 212 170 240 40 280 Z" fill="var(--swoosh)"/>
    </svg>

    <div class="brand">
      <span class="brand__dot"></span>
      <span class="brand__name">Glimworld</span>
    </div>

    <p class="tagline">Culturally Immersive Language Learning Games</p>
    <p class="website">www.glimworld-play.com</p>
  </section>

</body>
</html>
```